i would like a business card to leave with customers and potential customers for electrical work and for the supply and install of reverse cycle airconditioning in the domestic and commercial market.
I own my own business and im a sole trader. I have an a'class electrical lisence and also a refrigeration lisence so i am
able to offer complete installations in airconditioning by a fully qualified and lisenced tradesman.
im looking for something that comes across as unique and professional.
i had the coluor black and some gold in mind but open to any coluors.
something like Caldrevo Electrical & Refrigeration
or Lanterra Air.
i will use this design on a business card to advertise through summer to help generate installs through the busy season.

Target Market(s)

Mainly domestic house holds through summer who are in need of airconditioning and reliable information to acomadate thier cooling and heating requirements

Industry/Entity Type

Electrical

Requirements
Must have
• Business name- Caldrevo
My name- Mark Delford
My mobile no- 0438 517 290
My email- mrdelford@qelvo.com.au
Installation & Decomissioning of aiconditioning split systems
LIC NO: TRK 540316
Nice to have
• Caldrevo Electrical & Refrigeration

```html
<!DOCTYPE html>
<html lang="en">
<head>
<meta charset="utf-8">
<title>Caldrevo Electrical &amp; Refrigeration – Business Card</title>
<link rel="stylesheet" href="https://fonts.googleapis.com/css2?family=Tinos:wght@400;700&family=PT+Sans+Narrow&family=Source+Sans+3:wght@400&display=swap">
<style>
  :root {
    --ink: #000000;
    --gold: #d1a650;
    --gold-text: #c9a457;
  }
  html, body {
    margin: 0;
    padding: 0;
    background: var(--ink);
    overflow: hidden;
  }
  .canvas {
    position: relative;
    width: 1200px;
    height: 1015px;
    background: var(--ink);
    overflow: hidden;
    color: var(--gold-text);
  }
  .brand-mark {
    position: absolute;
    left: 38px;
    top: 210px;
    width: 300px;
    text-align: center;
    font-family: "Tinos", "Times New Roman", serif;
    font-size: 50px;
    color: var(--gold);
    line-height: 1;
  }
  .licence {
    position: absolute;
    left: 39px;
    top: 454px;
    font-family: "PT Sans Narrow", "Arial Narrow", sans-serif;
    font-size: 39px;
    line-height: 1;
    color: var(--gold-text);
    white-space: nowrap;
  }
  .divider {
    position: absolute;
    left: 395px;
    top: 23px;
    width: 2px;
    height: 465px;
    background: var(--gold);
  }
  .card-info {
    position: absolute;
    left: 420px;
    top: 0;
    width: 760px;
    font-family: "Tinos", "Times New Roman", serif;
  }
  .company-name {
    position: absolute;
    top: 52px;
    left: 0;
    width: 760px;
    margin: 0;
    text-align: center;
    font-weight: 400;
    font-size: 48px;
    line-height: 1;
    white-space: nowrap;
  }
  .services {
    position: absolute;
    top: 143px;
    left: 0;
    width: 705px;
    margin: 0;
    text-align: center;
    font-size: 35px;
    line-height: 51px;
  }
  .owner {
    position: absolute;
    top: 298px;
    left: 0;
    width: 728px;
    margin: 0;
    text-align: center;
    font-weight: 700;
    font-size: 31px;
    letter-spacing: 2.5px;
    line-height: 1;
  }
  .contact {
    position: absolute;
    top: 400px;
    left: 24px;
    margin: 0;
    font-weight: 700;
    font-size: 32px;
    letter-spacing: 3.5px;
    line-height: 42px;
    white-space: nowrap;
  }
  .brand-panel {
    position: absolute;
    left: 23px;
    top: 528px;
    width: 318px;
    height: 466px;
    background: var(--gold);
    display: flex;
    align-items: center;
    justify-content: center;
  }
  .brand-panel-name {
    font-family: "Tinos", "Times New Roman", serif;
    font-size: 56px;
    color: var(--ink);
    line-height: 1;
  }
  .lockup-name {
    position: absolute;
    left: 352px;
    top: 632px;
    margin: 0;
    font-family: "Source Sans 3", "Myriad Pro", sans-serif;
    font-weight: 400;
    font-size: 57px;
    line-height: 1;
    color: var(--gold);
    white-space: nowrap;
  }
</style>
</head>
<body>
  <main class="canvas">
    <div class="brand-mark">Caldrevo</div>
    <div class="licence">LIC NO: TRK 540316</div>

    <div class="divider"></div>

    <section class="card-info">
      <h1 class="company-name">Caldrevo Electrical &amp; Refrigeration</h1>
      <p class="services">Installation &amp; Decomissioning of<br>airconditioning split systems</p>
      <p class="owner">Mark Delford</p>
      <p class="contact">Mob.: 0438 517 290<br>email: mrdelford@qelvo.com.au</p>
    </section>

    <div class="brand-panel">
      <span class="brand-panel-name">Caldrevo</span>
    </div>
    <p class="lockup-name">Caldrevo Electrical &amp; Refrigeration</p>
  </main>
</body>
</html>
```